Redesign Digital Lending Mobile App - Android/ Flutter

Want to re-theme an existing Digital Lending Mobile app to simplify customer journeys, as well as uplift the UI.

Most users will have small screen phones so the design needs to take that into consideration while also adapting to those with larger devices, like admins with Tablets.

Have already laid out customer journeys on Figma with guidance on how the flow of the app should be. https://www.plankora.example/board/q4ZtRm81KdWe7YhXcvBnaL/LoomKit?frame-id=3-5182&s=Jk2pQwEr7TyUi-9

Video capture of current app: https://vaultbin.example/clip/7Hx3LmQp9RtZw2KcVn4YsBd8EfGj1/play
https://vaultbin.example/clip/4PsWq8ZnTk2LrXy6MbJc3VhGd9FeA/play

The documented views for Web are also here https://docshelf.example/open?ref=3B8F2204AD7C91E5!tk8d1f6a2c4e7b90d3f5a1c8e2b6d4f9a07&cid=3b8f2204ad7c91e5&kind=file%2Cdocx&wdo=2

Target Market(s)

Kenya, Tanzania, Uganda - Africa

Industry/Entity Type

Fintech

Requirements
Must have
• Responsive for diff screens, esp. in context of smaller screen smartphone
Nice to have
• Thematic components to ensure new views can easily be adapted to these themse

```html
<!DOCTYPE html>
<html lang="en">
<head>
<meta charset="utf-8">
<title>LoomKit – Lending App Screens</title>
<link href="https://fonts.googleapis.com/css2?family=Open+Sans:wght@400;500;600;700&display=swap" rel="stylesheet">
<style>
:root{
  --stage:#2f7d74;
  --screen-bg:#f3f4f5;
  --surface:#ffffff;
  --ink:#2b2b2b;
  --ink-soft:#555a60;
  --line:#e3e5e8;
  --blue:#1e5fc6;
  --blue-soft:#e9f1fb;
  --blue-edge:#cddff5;
  --green:#3c9a5d;
  --green-soft:#e7f5e9;
  --green-edge:#cbe8d0;
  --track:#e6e8eb;
  --nav-icon:#4a4d52;
}
*{box-sizing:border-box;margin:0;padding:0}
html,body{width:1200px;height:727px;overflow:hidden}
body{background:var(--stage);font-family:"Open Sans",Arial,sans-serif;color:var(--ink);position:relative}
.screen{position:absolute;top:93px;width:263px;height:570px;background:var(--screen-bg);border-radius:26px;overflow:hidden}
.screen--home{left:113px}
.screen--summary{left:482px}
.screen--report{left:850px}
.abs{position:absolute}
.app-header{position:absolute;left:0;top:0;width:100%;height:70px;background:var(--surface)}
.header-title{position:absolute;top:32px;width:100%;text-align:center;font-size:12px;font-weight:500;letter-spacing:.3px}
.header-actions{position:absolute;right:12px;top:34px;display:flex;gap:10px}
.header-actions svg{width:12px;height:12px;fill:var(--nav-icon)}
.search-btn{position:absolute;left:13px;top:35px;width:12px;height:12px}
.brand{position:absolute;top:35px;left:96px;display:flex;align-items:center;gap:4px}
.brand-dot{width:18px;height:18px;border-radius:50%;background:var(--blue)}
.brand-name{font-size:12px;font-weight:700;color:var(--blue)}
.section-label{position:absolute;left:13px;font-size:11px;font-weight:500}
.filters{position:absolute;left:13px;right:13px;display:flex;gap:4px;height:19px}
.filter{background:var(--surface);border:1px solid var(--line);font-size:7px;color:var(--ink-soft);display:flex;align-items:center;justify-content:space-between;padding:0 5px}
.filter::after{content:"";border-left:3px solid transparent;border-right:3px solid transparent;border-top:4px solid var(--ink-soft)}
.stat-row{position:absolute;left:13px;right:13px;display:flex;gap:4px}
.stat-card{flex:1;background:var(--surface);border:1px solid var(--line);text-align:center;padding-top:6px;height:54px}
.stat-card svg{width:14px;height:14px}
.stat-label{font-size:8px;color:var(--ink-soft);line-height:12px}
.stat-value{font-size:8.5px;color:var(--ink);line-height:14px}
.metric{position:absolute;left:14px;width:226px;height:30px}
.metric-icon{position:absolute;left:0;top:-2px;width:20px;height:20px;border-radius:50%;background:var(--surface);box-shadow:0 0 0 1px var(--line);display:flex;align-items:center;justify-content:center}
.metric-icon span{width:9px;height:9px;border-radius:50%}
.metric-text{position:absolute;left:26px;top:-1px;font-size:9.5px;white-space:nowrap}
.metric-text b{font-weight:500}
.metric-text .blue{color:var(--blue)}
.metric-text .green{color:var(--green)}
.metric-track{position:absolute;left:26px;top:18px;width:196px;height:3px;background:var(--track);border-radius:2px}
.metric-fill{position:absolute;left:0;top:0;height:3px;border-radius:2px}
.metric-fill::after{content:"";position:absolute;right:-3px;top:-2px;width:7px;height:7px;border-radius:50%;background:#fff;box-shadow:0 0 0 1px var(--line)}
.chart-card{position:absolute;background:var(--surface)}
.btn-next{position:absolute;height:21px;width:57px;background:var(--green);color:#fff;font-size:11px;font-weight:500;border-radius:2px;display:flex;align-items:center;justify-content:center}
.bottom-nav{position:absolute;left:0;bottom:0;width:100%;height:44px;background:var(--surface);display:flex;justify-content:space-around;align-items:center;padding:0 6px 4px}
.bottom-nav svg{width:17px;height:17px;fill:var(--nav-icon)}
.bottom-nav .active{fill:var(--green)}
.detail-table{position:absolute;left:13px;top:151px;width:235px}
.detail-row{display:flex;gap:4px;height:21px;margin-bottom:2.5px;font-size:8.5px}
.detail-key{width:116px;display:flex;align-items:center;padding-left:7px;color:var(--ink-soft)}
.detail-key.k-blue{background:var(--blue-soft);border:1px solid var(--blue-edge)}
.detail-key.k-green{background:var(--green-soft);border:1px solid var(--green-edge)}
.detail-val{flex:1;background:var(--surface);border:1px solid var(--line);display:flex;align-items:center;padding-left:7px;color:var(--ink-soft)}
.total-title{position:absolute;top:80px;width:100%;text-align:center;color:var(--blue);font-size:11px;font-weight:500}
.total-box{position:absolute;left:55px;top:102px;width:151px;height:24px;background:var(--surface);border:1px solid var(--line);font-size:10px;display:flex;align-items:center;justify-content:center}
.toggle{position:absolute;top:213px;height:21px;width:57px;font-size:11px;font-weight:500;display:flex;align-items:center;justify-content:center;border-radius:2px}
.toggle--on{left:71px;background:var(--green);color:#fff}
.toggle--off{left:132px;background:#cfe9d5;color:var(--ink-soft);border:1px solid var(--green-edge)}
.period{position:absolute;top:255px;height:18px;display:flex;gap:4px;left:12px}
.period .filter{font-size:7px}
.finance-row{position:absolute;left:12px;right:12px;top:386px;display:flex;gap:4px}
.finance-row .stat-card{height:54px}
</style>
</head>
<body>

<svg width="0" height="0" style="position:absolute">
  <defs>
    <symbol id="i-bell" viewBox="0 0 24 24"><path d="M12 2a2 2 0 0 1 2 2v1a6 6 0 0 1 4 6v5l2 2v1H4v-1l2-2v-5a6 6 0 0 1 4-6V4a2 2 0 0 1 2-2zm-2 19h4a2 2 0 0 1-4 0z"/></symbol>
    <symbol id="i-user" viewBox="0 0 24 24"><circle cx="12" cy="7" r="5"/><path d="M3 22c0-5 4-8 9-8s9 3 9 8z"/></symbol>
    <symbol id="i-home" viewBox="0 0 24 24"><path d="M12 2 1 12h3v10h6v-6h4v6h6V12h3z"/></symbol>
    <symbol id="i-loan" viewBox="0 0 24 24"><circle cx="14" cy="7" r="6"/><path d="M1 15h5l5 2h6a2 2 0 0 1 0 3H9v1h9l5-4v4l-5 3H1z"/><path d="M13 4h3v1.5h-2.5v1H16V10h-3V8.5h2.5v-1H13z" fill="#fff"/></symbol>
    <symbol id="i-doc" viewBox="0 0 24 24"><path d="M3 2h13v8l-6 6-1 5H3zM6 6h7v2H6zm0 4h7v2H6zm0 4h4v2H6z" fill-rule="evenodd"/><path d="M20 9l3 3-9 9h-3v-3z"/></symbol>
    <symbol id="i-chart" viewBox="0 0 24 24"><path d="M2 22h3v-6H2zm5 0h3v-9H7zm5 0h3v-7h-3zm5 0h3V9h-3zM2 12l6-5 4 3 8-7 1 1-9 8-4-3-5 4z"/></symbol>
    <symbol id="i-gear" viewBox="0 0 24 24"><path d="M10 1h4l.6 3 2.3 1 2.6-1.7 2.8 2.8L20.6 8.7l1 2.3 3 .6v4l-3 .6-1 2.3 1.7 2.6-2.8 2.8-2.6-1.7-2.3 1-.6 3h-4l-.6-3-2.3-1-2.6 1.7-2.8-2.8 1.7-2.6-1-2.3-3-.6v-4l3-.6 1-2.3L1.9 6.1l2.8-2.8 2.6 1.7 2.3-1zM12 8a4 4 0 1 0 0 8 4 4 0 0 0 0-8z" transform="scale(.95) translate(.5 .5)"/></symbol>
  </defs>
</svg>

<!-- Home dashboard -->
<section class="screen screen--home">
  <header class="app-header">
    <div class="brand"><span class="brand-dot"></span><span class="brand-name">LoomKit</span></div>
    <div class="header-actions"><svg><use href="#i-bell"/></svg><svg><use href="#i-user"/></svg></div>
  </header>

  <div class="stat-row" style="top:82px">
    <div class="stat-card"><svg viewBox="0 0 24 24" fill="none" stroke="var(--blue)" stroke-width="2"><circle cx="12" cy="12" r="9"/><path d="M14 9h-3a1.5 1.5 0 0 0 0 3h2a1.5 1.5 0 0 1 0 3h-3M12 7v10"/></svg><div class="stat-label">Disbursed</div><div class="stat-value">$30k</div></div>
    <div class="stat-card"><svg viewBox="0 0 24 24" fill="none" stroke="var(--green)" stroke-width="2"><circle cx="12" cy="8" r="5"/><path d="M2 14l4 7M22 14l-4 7M6 13l4 4M18 13l-4 4"/></svg><div class="stat-label">Collected</div><div class="stat-value">$20k</div></div>
    <div class="stat-card"><svg viewBox="0 0 24 24" fill="none" stroke="var(--blue)" stroke-width="2"><circle cx="10" cy="7" r="4"/><path d="M3 21c0-5 3-8 7-8s7 3 7 8z"/><circle cx="17" cy="16" r="3"/></svg><div class="stat-label">Active Clients</div><div class="stat-value">50</div></div>
    <div class="stat-card"><svg viewBox="0 0 24 24" fill="none" stroke="var(--green)" stroke-width="2"><path d="M12 3l2.7 6 6.3.6-4.8 4.2 1.4 6.2L12 16.8 6.4 20l1.4-6.2L3 9.6 9.3 9z"/></svg><div class="stat-label">New Clients</div><div class="stat-value">30</div></div>
  </div>

  <div class="section-label" style="top:146px">Filters</div>
  <div class="filters" style="top:168px">
    <div class="filter" style="width:70px">Loan Officer</div>
    <div class="filter" style="width:59px">Branch</div>
    <div class="filter" style="width:45px">Fund</div>
    <div class="filter" style="flex:1">Product</div>
  </div>

  <div class="metric" style="top:207px"><div class="metric-icon"><span style="background:var(--blue)"></span></div><div class="metric-text">Near Due:&nbsp; <b class="blue">$2.5M</b></div><div class="metric-track"><div class="metric-fill" style="width:101px;background:var(--blue)"></div></div></div>
  <div class="metric" style="top:246px"><div class="metric-icon"><span style="background:var(--green)"></span></div><div class="metric-text">Due:&nbsp; <b class="green">$35K</b></div><div class="metric-track"><div class="metric-fill" style="width:60px;background:var(--green)"></div></div></div>
  <div class="metric" style="top:286px"><div class="metric-icon"><span style="background:var(--blue);border-radius:2px"></span></div><div class="metric-text">Overdue:&nbsp; <b class="blue">$2.5M</b></div><div class="metric-track"><div class="metric-fill" style="width:101px;background:var(--blue)"></div></div></div>
  <div class="metric" style="top:324px"><div class="metric-icon"><span style="background:var(--green)"></span></div><div class="metric-text">Pending Disbursement&nbsp; :&nbsp; <b class="green">$35K</b></div><div class="metric-track"><div class="metric-fill" style="width:65px;background:var(--green)"></div></div></div>
  <div class="metric" style="top:363px"><div class="metric-icon"><span style="background:var(--blue)"></span></div><div class="metric-text">Active Loans :&nbsp; <b class="blue">$2.5M</b></div><div class="metric-track"><div class="metric-fill" style="width:101px;background:var(--blue)"></div></div></div>

  <div class="chart-card" style="left:34px;top:400px;width:194px;height:90px">
    <svg width="194" height="90" viewBox="0 0 194 90">
      <defs><linearGradient id="g-home" x1="0" y1="0" x2="0" y2="1"><stop offset="0" stop-color="#4b7fe0" stop-opacity=".55"/><stop offset="1" stop-color="#4b7fe0" stop-opacity=".05"/></linearGradient></defs>
      <path d="M17.5 72 L35 40 L56 29 L78 44.5 L113 46 L140 33.5 L165 47 L178 72 Z" fill="url(#g-home)"/>
      <polyline points="17.5,72 35,40 56,29 78,44.5 113,46 140,33.5 165,47 178,72" fill="none" stroke="var(--blue)" stroke-width="1.8"/>
      <g fill="#fff" stroke="#8aa6e0" stroke-width="1.2"><circle cx="35" cy="40" r="2.5"/><circle cx="56" cy="29" r="2.5"/><circle cx="78" cy="44.5" r="2.5"/><circle cx="113" cy="46" r="2.5"/><circle cx="140" cy="33.5" r="2.5"/><circle cx="165" cy="47" r="2.5"/></g>
      <rect x="48" y="7" width="16" height="9" rx="2" fill="#eceef1"/>
      <text x="56" y="14" font-size="6" text-anchor="middle" fill="#333">448</text>
      <g font-size="4.5" fill="#777" text-anchor="middle"><text x="18" y="82">01</text><text x="35.5" y="82">02</text><text x="53" y="82">03</text><text x="71" y="82">04</text><text x="89" y="82">05</text><text x="107" y="82">06</text><text x="125" y="82">07</text><text x="142" y="82">08</text><text x="160" y="82">09</text><text x="178" y="82">10</text></g>
    </svg>
  </div>

  <div class="btn-next" style="left:103px;top:497px">Next</div>

  <nav class="bottom-nav">
    <svg class="active"><use href="#i-home"/></svg><svg><use href="#i-loan"/></svg><svg><use href="#i-doc"/></svg><svg><use href="#i-chart"/></svg><svg><use href="#i-gear"/></svg>
  </nav>
</section>

<!-- Loan summary -->
<section class="screen screen--summary">
  <header class="app-header">
    <svg class="search-btn" viewBox="0 0 24 24" fill="none" stroke="var(--nav-icon)" stroke-width="2.5"><circle cx="10" cy="10" r="7"/><path d="M15 15l7 7"/></svg>
    <div class="header-title">LOAN SUMMARY</div>
    <div class="header-actions"><svg><use href="#i-bell"/></svg><svg><use href="#i-user"/></svg></div>
  </header>

  <div class="section-label" style="top:86px">Filters</div>
  <div class="filters" style="top:108px">
    <div class="filter" style="width:70px">Loan Officer</div>
    <div class="filter" style="width:59px">Branch</div>
    <div class="filter" style="width:45px">Fund</div>
    <div class="filter" style="flex:1">Product</div>
  </div>

  <div class="detail-table">
    <div class="detail-row"><div class="detail-key k-blue">Loan reference number</div><div class="detail-val">3213</div></div>
    <div class="detail-row"><div class="detail-key k-green">Loan status</div><div class="detail-val">Active</div></div>
    <div class="detail-row"><div class="detail-key k-blue">Date disbursed</div><div class="detail-val">13 July 2024</div></div>
    <div class="detail-row"><div class="detail-key k-green">Date approved</div><div class="detail-val">24 July 2024</div></div>
    <div class="detail-row"><div class="detail-key k-blue">Last repayment date</div><div class="detail-val">13 October 2024</div></div>
    <div class="detail-row"><div class="detail-key k-green">Next repayment date</div><div class="detail-val">24 October 2024</div></div>
    <div class="detail-row"><div class="detail-key k-blue">Amount disbursed</div><div class="detail-val">35,00,000</div></div>
    <div class="detail-row"><div class="detail-key k-green">Amount outstanding</div><div class="detail-val">35,00,000</div></div>
    <div class="detail-row"><div class="detail-key k-blue">Overdue days</div><div class="detail-val">45</div></div>
  </div>

  <div class="btn-next" style="left:103px;top:382px">Next</div>

  <nav class="bottom-nav">
    <svg><use href="#i-home"/></svg><svg><use href="#i-loan"/></svg><svg class="active"><use href="#i-doc"/></svg><svg><use href="#i-chart"/></svg><svg><use href="#i-gear"/></svg>
  </nav>
</section>

<!-- Report -->
<section class="screen screen--report">
  <header class="app-header">
    <div class="header-title">REPORT</div>
    <div class="header-actions"><svg><use href="#i-bell"/></svg><svg><use href="#i-user"/></svg></div>
  </header>

  <div class="total-title">Total Loan</div>
  <div class="total-box">$ 35,00,000</div>

  <div class="section-label" style="top:140px;left:12px">Filters</div>
  <div class="filters" style="top:162px;left:12px;right:12px">
    <div class="filter" style="width:70px">Loan Officer</div>
    <div class="filter" style="width:59px">Branch</div>
    <div class="filter" style="width:45px">Fund</div>
    <div class="filter" style="flex:1">Product</div>
  </div>

  <div class="toggle toggle--on">Profit</div>
  <div class="toggle toggle--off">Loss</div>

  <div class="period">
    <div class="filter" style="width:44px">Month</div>
    <div class="filter" style="width:46px">Jul 2024</div>
  </div>

  <div class="chart-card" style="left:12px;top:284px;width:236px;height:88px">
    <svg width="236" height="88" viewBox="0 0 236 88">
      <defs><linearGradient id="g-report" x1="0" y1="0" x2="0" y2="1"><stop offset="0" stop-color="#5a86e6" stop-opacity=".35"/><stop offset="1" stop-color="#5a86e6" stop-opacity="0"/></linearGradient></defs>
      <path d="M15 43 C30 38 45 36 60 39 C75 42 85 46 100 42 C115 38 128 22 146 22 C164 22 172 34 190 35 C205 36 213 30 221 27 L221 56 L15 56 Z" fill="url(#g-report)"/>
      <g stroke="#dde3ee" stroke-width=".6"><line x1="49" y1="38" x2="49" y2="56"/><line x1="85" y1="44" x2="85" y2="56"/><line x1="118" y1="36" x2="118" y2="56"/><line x1="153" y1="23" x2="153" y2="56"/><line x1="188" y1="35" x2="188" y2="56"/><line x1="221" y1="27" x2="221" y2="56"/></g>
      <path d="M15 43 C30 38 45 36 60 39 C75 42 85 46 100 42 C115 38 128 22 146 22 C164 22 172 34 190 35 C205 36 213 30 221 27" fill="none" stroke="var(--blue)" stroke-width="2"/>
      <g font-size="5.5" fill="#555" text-anchor="middle"><text x="18" y="67">Week 1</text><text x="86" y="67">Week 2</text><text x="153" y="67">Week 3</text><text x="220" y="67">Week 4</text></g>
    </svg>
  </div>

  <div class="finance-row">
    <div class="stat-card"><svg viewBox="0 0 24 24" fill="none" stroke="var(--blue)" stroke-width="2"><circle cx="11" cy="10" r="7"/><path d="M13 7h-3a1.5 1.5 0 0 0 0 3h2a1.5 1.5 0 0 1 0 3H9M11 5v10M4 21l6-4h6"/></svg><div class="stat-label">Revenue</div><div class="stat-value">$3000</div></div>
    <div class="stat-card"><svg viewBox="0 0 24 24" fill="none" stroke="var(--green)" stroke-width="2"><rect x="2" y="9" width="18" height="12" rx="2"/><path d="M5 9l9-6 3 6M16 15h6"/></svg><div class="stat-label">Expenses</div><div class="stat-value">$3000</div></div>
    <div class="stat-card"><svg viewBox="0 0 24 24" fill="none" stroke="var(--blue)" stroke-width="2"><path d="M6 3h8l5 5v13H6z"/><path d="M9 17l6-6"/><circle cx="10" cy="12" r="1"/><circle cx="14" cy="16" r="1"/></svg><div class="stat-label">Tax</div><div class="stat-value">$3000</div></div>
    <div class="stat-card"><svg viewBox="0 0 24 24" fill="none" stroke="var(--green)" stroke-width="2"><rect x="2" y="6" width="20" height="12" rx="1"/><circle cx="12" cy="12" r="3"/><path d="M5 9v6M19 9v6"/></svg><div class="stat-label">Salaries</div><div class="stat-value">$3000</div></div>
  </div>

  <nav class="bottom-nav">
    <svg><use href="#i-home"/></svg><svg><use href="#i-loan"/></svg><svg><use href="#i-doc"/></svg><svg class="active"><use href="#i-chart"/></svg><svg><use href="#i-gear"/></svg>
  </nav>
</section>

</body>
</html>
```